business card

Business card for new business.
Red and black corporate colors.
Card can have an Indsutrial feel to it. Feel free to add Rust, Bolted steel, or graphics as you see fit. We provide highly specialized services to the below mentioned industries.
Keep information out of corners so that if I want I can choose rounded corners.
Information
- front. name - title - phone - email
- Rear
Refining - Rail - Infrastructure - Mining - Energy
Calgary - Edmonton - Fort McMurray - Revelstoke - Vancouver

```html
<!DOCTYPE html>
<html lang="en">
<head>
<meta charset="UTF-8">
<title>Ironvale Business Card</title>
<link href="https://fonts.googleapis.com/css2?family=Lato:wght@400;700;900&display=swap" rel="stylesheet">
<style>
  :root {
    --ink: #000000;
    --paper: #ffffff;
    --signal-red: #e21d25;
    --steel-grey: #8a8a8a;
    --backdrop: #d9d9d9;
  }
  * { margin: 0; padding: 0; box-sizing: border-box; }
  html, body {
    width: 1200px;
    height: 1059px;
    overflow: hidden;
    background: var(--backdrop);
    font-family: "Lato", Arial, sans-serif;
  }
  .canvas {
    position: relative;
    width: 1200px;
    height: 1059px;
  }
  .card {
    position: absolute;
    left: 190px;
    width: 820px;
    height: 469px;
    overflow: hidden;
    box-shadow: 0 10px 30px rgba(0,0,0,0.25);
  }
  .card--back { top: 40px; background: var(--ink); }
  .card--front { top: 549px; background: var(--paper); }

  .wordmark {
    display: flex;
    align-items: center;
    gap: 14px;
    color: var(--steel-grey);
    font-weight: 900;
    letter-spacing: 2px;
    text-transform: uppercase;
    white-space: nowrap;
  }
  .wordmark__mark {
    width: 18px;
    height: 18px;
    background: var(--signal-red);
  }

  .card--back .wordmark {
    position: absolute;
    left: 0; right: 0;
    top: 150px;
    justify-content: center;
    font-size: 72px;
  }
  .card--back .wordmark__mark { width: 26px; height: 26px; }

  .service-lines {
    position: absolute;
    left: 0; right: 0;
    top: 305px;
    text-align: center;
    color: var(--paper);
    font-size: 22px;
    line-height: 1.5;
    white-space: nowrap;
  }
  .dot {
    display: inline-block;
    width: 7px;
    height: 7px;
    border-radius: 50%;
    background: var(--signal-red);
    margin: 0 8px;
    vertical-align: middle;
  }

  .logo-block {
    position: absolute;
    left: 0;
    top: 170px;
    width: 380px;
    height: 240px;
    background: var(--ink);
    display: flex;
    align-items: center;
    justify-content: center;
  }
  .logo-block .wordmark { font-size: 44px; gap: 10px; }
  .logo-block .wordmark__mark { width: 16px; height: 16px; }

  .contact-panel {
    position: absolute;
    left: 380px;
    top: 50px;
    width: 440px;
    height: 280px;
    background: var(--signal-red);
    color: var(--paper);
    padding: 30px 0 0 72px;
  }
  .contact-panel::before {
    content: "";
    position: absolute;
    left: 42px;
    top: 28px;
    bottom: 28px;
    width: 2px;
    background: var(--paper);
  }
  .contact-name { font-size: 27px; font-weight: 700; }
  .contact-title { font-size: 18px; margin-top: 4px; }
  .contact-address { font-size: 19px; margin-top: 12px; line-height: 1.3; }
  .contact-list { list-style: none; margin-top: 12px; }
  .contact-list li {
    display: flex;
    align-items: center;
    gap: 12px;
    font-size: 19px;
    line-height: 1.4;
  }
  .contact-list svg { width: 16px; height: 16px; fill: var(--paper); flex: none; }
</style>
</head>
<body>
<div class="canvas">

  <section class="card card--back">
    <div class="wordmark"><span class="wordmark__mark"></span>Ironvale</div>
    <div class="service-lines">
      <p>Fabrication<span class="dot"></span>Pipelines<span class="dot"></span>Utilities<span class="dot"></span>Marine<span class="dot"></span>Power</p>
      <p>Redmere<span class="dot"></span>Ashford Bay<span class="dot"></span>Northcliff<span class="dot"></span>Stonebridge<span class="dot"></span>Westhaven</p>
    </div>
  </section>

  <section class="card card--front">
    <div class="logo-block">
      <div class="wordmark"><span class="wordmark__mark"></span>Ironvale</div>
    </div>
    <div class="contact-panel">
      <p class="contact-name">Daniel Crofton</p>
      <p class="contact-title">Manager</p>
      <p class="contact-address">418 Harbor Lane<br>Austin, TX 78701</p>
      <ul class="contact-list">
        <li>
          <svg viewBox="0 0 24 24" aria-hidden="true"><path d="M6.6 10.8a15.5 15.5 0 0 0 6.6 6.6l2.2-2.2c.3-.3.7-.4 1-.2 1.1.4 2.3.6 3.6.6.6 0 1 .4 1 1V20c0 .6-.4 1-1 1A17 17 0 0 1 3 4c0-.6.4-1 1-1h3.5c.6 0 1 .4 1 1 0 1.3.2 2.5.6 3.6.1.3 0 .7-.2 1z"/></svg>
          512 555 0148
        </li>
        <li>
          <svg viewBox="0 0 24 24" aria-hidden="true"><path d="M2 5h20v14H2z M3.5 6.5 12 13l8.5-6.5" fill="none" stroke="#fff" stroke-width="2"/></svg>
          info@ironvale.com
        </li>
        <li>
          <svg viewBox="0 0 24 24" aria-hidden="true"><circle cx="12" cy="12" r="9" fill="none" stroke="#fff" stroke-width="2"/><path d="M3 12h18M12 3c3 3 3 15 0 18M12 3c-3 3-3 15 0 18" fill="none" stroke="#fff" stroke-width="1.6"/></svg>
          www.ironvale.com
        </li>
      </ul>
    </div>
  </section>

</div>
</body>
</html>
```